Classy, Elegant, Simple Business Card Design

Looking to have a classy, simple, and elegant design. Want a top notch designed business card. I really like the look of the new torvane credit card. I also like the design I attached. I am trying to reach 21-29 year old females for booking us for there wedding or event. We offer Disc Jockey Service, Photo Booth Rentals, and Uplighting .

Target Market(s)

21-28 year old females

Contact Information for Business Card

Has to have logo, website, email, and phone number

Font styles to use
Other font styles liked:
• open to font choice, modern, clean
Designer to choose
33a6d7
0791cd
0555a3
ffffff

Requirements
Must have
• Has to have logo, website, email, and phone number
Nice to have
• I really like the design of the new torvane credit card. I also included my logo and some designs I like
Should not have
• clutter or too much info

```html
<!DOCTYPE html>
<html lang="en">
<head>
<meta charset="utf-8">
<title>Tidelight Event Group – Business Cards</title>
<link rel="stylesheet" href="https://fonts.googleapis.com/css2?family=Lato:wght@300;400;700&display=swap">
<style>
  :root {
    --backdrop: #3a3330;
    --card: #0c0c0d;
    --card-edge: #1c1c1e;
    --blue-light: #33a6d7;
    --blue: #0791cd;
    --blue-deep: #0555a3;
    --white: #ffffff;
    --grey: #8d8f93;
    --silver: #d9dadc;
    --rule: #3a3b3e;
  }
  * { margin: 0; padding: 0; box-sizing: border-box; }
  html, body {
    width: 1200px; height: 844px; overflow: hidden;
    background: var(--backdrop);
    font-family: "Lato", Arial, sans-serif;
  }
  .stage {
    position: relative; width: 1200px; height: 844px;
    display: flex; align-items: center; justify-content: center; gap: 60px;
  }
  .card {
    position: relative; width: 520px; height: 300px;
    background: var(--card);
    border: 1px solid var(--card-edge);
    box-shadow: 0 18px 40px rgba(0,0,0,.45);
  }
  /* Front */
  .brand {
    position: absolute; left: 0; right: 0; top: 86px;
    display: flex; flex-direction: column; align-items: center;
  }
  .brand-row { display: flex; align-items: center; gap: 12px; }
  .brand-dot {
    width: 16px; height: 16px; border-radius: 50%;
    background: var(--blue);
  }
  .brand-name {
    font-weight: 700; font-size: 38px; letter-spacing: 3px;
    color: var(--blue); text-transform: uppercase;
  }
  .brand-tagline {
    margin-top: 6px; font-weight: 300; font-size: 13px;
    letter-spacing: 6px; color: var(--grey); text-transform: uppercase;
  }
  .rule {
    position: absolute; height: 1px; background: var(--rule);
  }
  .front .rule { left: 34px; right: 34px; bottom: 58px; }
  .contact {
    position: absolute; left: 34px; bottom: 28px;
    font-size: 13.5px; color: var(--white); letter-spacing: .2px;
  }
  .contact .label { color: var(--blue-light); font-weight: 700; }
  .contact .accent { color: var(--blue-light); }
  .contact .sep { color: var(--grey); margin: 0 5px; }
  /* Back */
  .back .brand { top: 96px; }
  .back .brand-dot { background: var(--silver); }
  .back .brand-name { color: var(--silver); font-size: 34px; }
  .back .rule { left: 34px; right: 34px; bottom: 58px; }
  .services {
    position: absolute; left: 34px; bottom: 28px;
    font-size: 13.5px; color: var(--white); letter-spacing: .2px;
  }
  .services .sep { color: var(--grey); margin: 0 5px; }
</style>
</head>
<body>
<main class="stage">
  <section class="card front" aria-label="Card front">
    <div class="brand">
      <div class="brand-row">
        <span class="brand-dot"></span>
        <span class="brand-name">Tidelight</span>
      </div>
      <span class="brand-tagline">Event Group</span>
    </div>
    <div class="rule"></div>
    <p class="contact">
      <span class="label">P:</span> 044-987 654 321<span class="sep">|</span><span class="label">E:</span> hello@tidelight.com<span class="sep">|</span>www.<span class="accent">tidelightevents</span>.com
    </p>
  </section>

  <section class="card back" aria-label="Card back">
    <div class="brand">
      <div class="brand-row">
        <span class="brand-dot"></span>
        <span class="brand-name">Tidelight</span>
      </div>
    </div>
    <div class="rule"></div>
    <p class="services">
      Disc Jockey Service<span class="sep">|</span>Photo Booth Rentals<span class="sep">|</span>Uplighting
    </p>
  </section>
</main>
</body>
</html>
```